Larkfield Ridge Management

I need a professional website. My current website is larkfieldridgemanagement.com and I hate it. It was created with some AI tool very quickly because I needed a site up and running with no advanced notice. I’m open to all designs .. I trust you, the professionals will deliver the results I’m anxiously awaiting! :)

```html
<!DOCTYPE html>
<html lang="en">
<head>
<meta charset="utf-8">
<title>Larkfield Ridge Management — Property Management</title>
<link href="https://fonts.googleapis.com/css2?family=Inter:wght@400;500;600;700;800&display=swap" rel="stylesheet">
<style>
:root{
  --navy:#1f2d4d;
  --navy-2:#2a3f6e;
  --blue:#4a72c0;
  --red:#d32f2f;
  --ink:#1b1b1f;
  --muted:#4d5361;
  --soft:#eef3fc;
  --plate:#9aa3b6;
  --line:#dde2ea;
  --white:#ffffff;
}
*{margin:0;padding:0;box-sizing:border-box}
html,body{width:1200px;height:4717px;overflow:hidden}
body{font-family:"Inter",Arial,sans-serif;color:var(--ink);background:var(--white)}
.wrap{width:1000px;margin:0 auto;position:relative}
.accent{color:var(--red)}
.eyebrow{color:var(--red);font-size:15px;font-weight:500;text-transform:uppercase;letter-spacing:.3px}
.btn{display:inline-flex;align-items:center;gap:6px;font-size:16px;font-weight:600;border-radius:6px;padding:11px 22px;color:var(--white);background:var(--red);text-decoration:none}
.btn svg{width:12px;height:12px}
h2{font-size:40px;font-weight:700;line-height:1.22}

/* header */
.site-header{height:110px;display:flex;align-items:center;justify-content:space-between;padding:0 100px 0 84px}
.brand{display:flex;align-items:center;gap:12px;font-size:22px;font-weight:700;color:var(--navy)}
.brand-mark{width:22px;height:22px;background:var(--red)}
.nav{display:flex;align-items:center;gap:34px}
.nav ul{display:flex;gap:10px;list-style:none;font-size:16px;font-weight:500;color:var(--ink)}
.nav ul li{padding:0 2px}
.call{display:flex;align-items:center;gap:10px;background:var(--navy);color:var(--white);font-size:17px;font-weight:500;padding:15px 24px;border-radius:6px}
.call svg{width:16px;height:16px}

/* hero */
.hero{position:relative;height:643px;overflow:hidden}
.hero-photo{position:absolute;inset:0;background:linear-gradient(100deg,#22345f 0%,#2c4274 38%,#5e6d86 62%,#9aa0a8 82%,#6f7377 100%)}
.hero-copy{position:relative;padding:130px 0 0 100px;width:560px;color:var(--white)}
.hero h1{font-size:59px;font-weight:700;line-height:1.18}
.hero p{font-size:16px;line-height:1.5;margin-top:18px;width:480px}
.hero-actions{display:flex;gap:16px;margin-top:26px}
.btn-outline{background:transparent;border:2px solid var(--white)}

/* services */
.services{background:var(--soft);height:727px;text-align:center;padding-top:108px}
.services h2{margin-top:20px}
.services .intro{font-size:16.5px;line-height:1.5;color:var(--muted);width:860px;margin:22px auto 0;text-align:left}
.service-grid{display:grid;grid-template-columns:repeat(4,1fr);gap:16px;margin-top:40px}
.service-photo{height:210px;border-radius:14px}
.service-grid h3{font-size:19px;font-weight:600;margin-top:28px}
.services .btn{margin-top:52px;font-size:16px;padding:11px 28px}

/* feature rows */
.features{height:1250px;padding-top:140px}
.feature{display:flex;align-items:center;justify-content:space-between;height:440px}
.feature + .feature{margin-top:112px}
.feature-copy{width:480px}
.feature-copy h2{margin-top:16px}
.feature-copy p{font-size:16.5px;line-height:1.5;color:var(--muted);margin-top:20px}
.feature-copy .btn{margin-top:22px}
.framed{position:relative;width:438px;height:376px}
.framed::before{content:"";position:absolute;left:31px;right:31px;top:-31px;bottom:-31px;background:var(--plate);border-radius:18px}
.framed .photo{position:absolute;inset:0;border-radius:16px}
.feature.reverse .framed{margin-left:17px}

/* stats */
.stats{height:262px;background:linear-gradient(90deg,var(--navy) 0%,var(--navy-2) 45%,var(--blue) 100%);color:var(--white)}
.stats .wrap{display:grid;grid-template-columns:repeat(4,1fr);padding-top:48px;text-align:center}
.stat svg{width:76px;height:76px}
.stat strong{display:block;font-size:43px;font-weight:600;margin-top:8px;letter-spacing:.5px}
.stat span{display:block;font-size:16px;text-transform:uppercase;color:#cbd5ea;margin-top:10px}

/* testimonials */
.testimonials{height:635px;background:linear-gradient(160deg,#f5f7fb 0%,#e6ebf3 50%,#d7dee9 100%);text-align:center;padding-top:70px}
.testimonials h2{margin-top:20px}
.quote-card{width:832px;height:357px;margin:40px auto 0;background:var(--white);border-radius:16px;box-shadow:0 4px 22px rgba(31,45,77,.12);text-align:left;padding:30px 42px 0 32px;position:relative}
.quote-mark{width:40px;height:40px}
.stars{display:flex;gap:18px;margin:18px 0 0 10px}
.stars svg{width:22px;height:22px}
.quote-card blockquote{font-size:19.5px;font-weight:600;line-height:1.25;margin:22px 0 0 10px;width:690px}
.author{margin:45px 0 0 10px}
.author strong{font-size:19px;font-weight:600}
.author span{display:block;font-size:16px;color:var(--muted);margin-top:12px}
.arrows{position:absolute;right:46px;bottom:50px;display:flex;gap:16px}
.arrows span{width:40px;height:40px;border:1.5px solid #8a8f99;border-radius:50%;display:flex;align-items:center;justify-content:center}
.arrows svg{width:14px;height:14px}

/* contact */
.contact{height:696px;padding-top:105px}
.contact .wrap{display:flex;justify-content:space-between}
.contact-copy{width:470px}
.contact-copy h2{margin-top:24px}
.contact-copy p{font-size:16.5px;line-height:1.5;color:var(--muted);margin-top:22px}
.channels{list-style:none;margin-top:40px}
.channels li{display:flex;align-items:center;gap:24px;margin-bottom:28px}
.channels .icon{width:62px;height:62px;background:#585a5f;border-radius:6px;display:flex;align-items:center;justify-content:center}
.channels svg{width:28px;height:28px}
.channels small{display:block;color:var(--red);font-size:16px}
.channels b{display:block;font-size:16.5px;font-weight:500;margin-top:6px}
.form-card{width:496px;height:560px;border:2px solid var(--line);border-radius:26px;background:#f7f8fa;padding:40px 30px 0 30px;margin-top:-30px}
.form-grid{display:grid;grid-template-columns:1fr 1fr;gap:0 22px}
.field{margin-bottom:22px}
.field label{display:block;font-size:16px;margin:0 0 10px 6px}
.field .input{height:60px;background:var(--white);border:1.5px solid var(--line);border-radius:10px;font-size:11px;color:#9aa0aa;padding:22px 14px;display:flex;justify-content:space-between}
.field .input svg{width:14px;height:14px;margin-top:-2px}
.field.full{grid-column:1 / 3}
.field.full .input{height:136px;align-items:flex-start}
.form-card .submit{display:flex;justify-content:center;margin-top:20px}
.form-card .submit span{background:var(--navy);color:var(--white);font-size:16px;font-weight:600;padding:16px 28px;border-radius:6px;display:flex;gap:6px;align-items:center}
.form-card .submit svg{width:12px;height:12px}

/* footer */
.site-footer{height:394px;background:linear-gradient(90deg,var(--navy) 0%,var(--navy-2) 45%,var(--blue) 100%);color:var(--white);padding-top:58px}
.footer-top{display:flex}
.footer-brand{width:400px}
.footer-brand .brand{color:var(--white);font-size:24px;margin:18px 0 48px 6px}
.footer-brand ul{list-style:none}
.footer-brand li{display:flex;gap:10px;align-items:center;font-size:16.5px;margin-bottom:20px;padding-left:6px}
.footer-brand svg{width:16px;height:16px}
.footer-col{list-style:none;font-size:14px;color:#dbe3f3}
.footer-col h4{font-size:16.5px;font-weight:600;color:var(--white);margin:40px 0 14px}
.footer-col li{margin-bottom:17px}
.col-services{width:282px}
.col-company{width:188px}
.footer-bottom{border-top:1px solid rgba(255,255,255,.3);margin-top:30px;padding-top:20px;display:flex;justify-content:space-between;font-size:14px;color:#e6ebf5}
</style>
</head>
<body>

<header class="site-header">
  <div class="brand"><span class="brand-mark"></span>Larkfield Ridge</div>
  <nav class="nav">
    <ul><li>Home</li><li>About</li><li>Services</li><li>Contact</li></ul>
    <div class="call">
      <svg viewBox="0 0 24 24" fill="#fff"><path d="M6.6 10.8a15.1 15.1 0 0 0 6.6 6.6l2.2-2.2c.3-.3.7-.4 1-.2 1.1.4 2.3.6 3.6.6.6 0 1 .4 1 1V20c0 .6-.4 1-1 1A17 17 0 0 1 3 4c0-.6.4-1 1-1h3.5c.6 0 1 .4 1 1 0 1.3.2 2.5.6 3.6.1.3 0 .7-.2 1z"/></svg>
      (216) 555-0148
    </div>
  </nav>
</header>

<section class="hero">
  <div class="hero-photo" role="img" aria-label="Hand holding a pen over documents beside a small architectural model of a tall building"></div>
  <div class="hero-copy">
    <h1>Property Management Redefined</h1>
    <p>A true partner, not just a vendor. We apply rigorously tested frameworks and data-driven methodologies to safeguard property value while elevating tenant experience.</p>
    <div class="hero-actions">
      <span class="btn">Request a Proposal <svg viewBox="0 0 12 12" fill="none" stroke="#fff" stroke-width="2"><path d="M1 6h9M6 2l4 4-4 4"/></svg></span>
      <span class="btn btn-outline">Explore Services</span>
    </div>
  </div>
</section>

<section class="services">
  <div class="wrap">
    <div class="eyebrow">What we do</div>
    <h2>Strategic <span class="accent">Property</span> Management <span class="accent">Solutions</span></h2>
    <p class="intro">Our analysis demonstrates that effective property oversight originates from meticulous operational planning, transparent communication channels, and data-driven performance metrics across every asset class.</p>
    <div class="service-grid">
      <div><div class="service-photo" role="img" aria-label="Worker repairing tiles beside a pool under a patio" style="background:linear-gradient(160deg,#8c7560,#c9c1b4 55%,#bfe4e4)"></div><h3>Basic Service</h3></div>
      <div><div class="service-photo" role="img" aria-label="Water storage tank on a lawn beside a building" style="background:linear-gradient(160deg,#8fa0a8,#d3d8dc 50%,#6f9a4c)"></div><h3>Intermediate Service</h3></div>
      <div><div class="service-photo" role="img" aria-label="Model houses with digital analytics overlay" style="background:linear-gradient(160deg,#1b3550,#3d6a8c 55%,#cfd8e0)"></div><h3>Advanced Service</h3></div>
      <div><div class="service-photo" role="img" aria-label="Small house model on a desk with documents and handshake" style="background:linear-gradient(160deg,#6f6a68,#bcb8b4 50%,#3d5588)"></div><h3>Advanced + Service</h3></div>
    </div>
    <span class="btn">See Our Services <svg viewBox="0 0 12 12" fill="none" stroke="#fff" stroke-width="2"><path d="M1 6h9M6 2l4 4-4 4"/></svg></span>
  </div>
</section>

<section class="features">
  <div class="wrap">
    <div class="feature">
      <div class="feature-copy">
        <div class="eyebrow">About us</div>
        <h2>Our <span class="accent">Property</span><br><span class="accent">Management</span> Solutions</h2>
        <p>Our organization delivers comprehensive property management solutions that optimize asset performance and tenant satisfaction. By integrating advanced analytics with proven operational frameworks, our specialists ensure each property achieves sustained value appreciation.</p>
        <span class="btn">Read More <svg viewBox="0 0 12 12" fill="none" stroke="#fff" stroke-width="2"><path d="M1 6h9M6 2l4 4-4 4"/></svg></span>
      </div>
      <div class="framed" style="margin-right:32px">
        <div class="photo" role="img" aria-label="Agent handing a small house model to a client across a meeting table" style="background:linear-gradient(150deg,#6e5a4a,#b9aea3 45%,#dfe3e8 70%,#7d8796)"></div>
      </div>
    </div>
    <div class="feature reverse">
      <div class="framed">
        <div class="photo" role="img" aria-label="Small house models on stacks of coins with a hand holding a young tree" style="background:linear-gradient(150deg,#4a4d55,#8c8f94 40%,#e5e5e2 70%,#b69a63)"></div>
      </div>
      <div class="feature-copy" style="width:470px">
        <div class="eyebrow">Our expertise</div>
        <h2>Expertise <span class="accent">Rooted</span> in <span class="accent">Asset</span> Preservation</h2>
        <p>The organization applies rigorously tested frameworks and data-driven methodologies to safeguard property value while elevating tenant experience.</p>
        <span class="btn">Learn More <svg viewBox="0 0 12 12" fill="none" stroke="#fff" stroke-width="2"><path d="M1 6h9M6 2l4 4-4 4"/></svg></span>
      </div>
    </div>
  </div>
</section>

<section class="stats">
  <div class="wrap">
    <div class="stat">
      <svg viewBox="0 0 64 64" fill="none" stroke="#fff" stroke-width="2"><circle cx="32" cy="22" r="9"/><circle cx="32" cy="22" r="14" stroke-dasharray="4 3"/><circle cx="18" cy="42" r="5"/><circle cx="46" cy="42" r="5"/><path d="M10 60v-6a8 8 0 0 1 16 0v6M38 60v-6a8 8 0 0 1 16 0v6M24 60v-10a8 8 0 0 1 16 0v10"/></svg>
      <strong>2,400+</strong><span>Units under management</span>
    </div>
    <div class="stat">
      <svg viewBox="0 0 64 64" fill="none" stroke="#fff" stroke-width="2"><rect x="12" y="8" width="36" height="46"/><path d="M20 16h6v6h-6zM34 16h6v6h-6zM20 28h6v6h-6zM34 28h6v6h-6zM26 54v-10h8v10"/><circle cx="48" cy="48" r="10"/><path d="M44 52l8-8M44.5 44.5h.1M51.5 51.5h.1"/></svg>
      <strong>98%</strong><span>Average occupancy</span>
    </div>
    <div class="stat">
      <svg viewBox="0 0 64 64" fill="none" stroke="#fff" stroke-width="2"><path d="M32 6l3 6 6 1-4 4 1 6-6-3-6 3 1-6-4-4 6-1zM16 12l2 4 4 .5-3 3 .7 4-3.7-2-3.7 2 .7-4-3-3 4-.5zM48 12l2 4 4 .5-3 3 .7 4-3.7-2-3.7 2 .7-4-3-3 4-.5z"/><path d="M6 40h8v18H6zM14 44h14l8 3h8a3 3 0 0 1 0 6H30M14 56h22l20-10a3 3 0 0 0-3-5l-11 5"/></svg>
      <strong>15+</strong><span>Years of service</span>
    </div>
    <div class="stat">
      <svg viewBox="0 0 64 64" fill="none" stroke="#fff" stroke-width="2"><path d="M32 4l2 4 4 .5-3 3 .7 4-3.7-2-3.7 2 .7-4-3-3 4-.5zM18 8l1.6 3 3 .5-2.2 2 .5 3-2.9-1.5-2.9 1.5.5-3-2.2-2 3-.5zM46 8l1.6 3 3 .5-2.2 2 .5 3-2.9-1.5-2.9 1.5.5-3-2.2-2 3-.5z"/><circle cx="32" cy="30" r="6"/><circle cx="16" cy="34" r="5"/><circle cx="48" cy="34" r="5"/><path d="M22 60v-10a10 10 0 0 1 20 0v10M6 58v-6a8 8 0 0 1 14-5M58 58v-6a8 8 0 0 0-14-5"/></svg>
      <strong>4.9/5</strong><span>Client satisfaction</span>
    </div>
  </div>
</section>

<section class="testimonials">
  <div class="eyebrow">Testimonials</div>
  <h2><span class="accent">Trusted</span> by Property <span class="accent">Owners</span></h2>
  <article class="quote-card">
    <svg class="quote-mark" viewBox="0 0 40 40" fill="none" stroke="#e88a8a" stroke-width="2"><path d="M4 8h12v12c0 7-4 12-10 14M22 8h12v12c0 7-4 12-10 14"/></svg>
    <div class="stars">
      <svg viewBox="0 0 24 24" fill="#f2b705"><path d="M12 2l3 7 7 .6-5.3 4.6 1.7 7.3L12 17.8 5.6 21.5l1.7-7.3L2 9.6 9 9z"/></svg>
      <svg viewBox="0 0 24 24" fill="#f2b705"><path d="M12 2l3 7 7 .6-5.3 4.6 1.7 7.3L12 17.8 5.6 21.5l1.7-7.3L2 9.6 9 9z"/></svg>
      <svg viewBox="0 0 24 24" fill="#f2b705"><path d="M12 2l3 7 7 .6-5.3 4.6 1.7 7.3L12 17.8 5.6 21.5l1.7-7.3L2 9.6 9 9z"/></svg>
      <svg viewBox="0 0 24 24" fill="#f2b705"><path d="M12 2l3 7 7 .6-5.3 4.6 1.7 7.3L12 17.8 5.6 21.5l1.7-7.3L2 9.6 9 9z"/></svg>
      <svg viewBox="0 0 24 24" fill="#f2b705"><path d="M12 2l3 7 7 .6-5.3 4.6 1.7 7.3L12 17.8 5.6 21.5l1.7-7.3L2 9.6 9 9z"/></svg>
    </div>
    <blockquote>"Larkfield Ridge Management transformed how we view property management. Their attention to detail and proactive communication has saved us both time and money. They truly operate as an extension of our team."</blockquote>
    <div class="author"><strong>Daniel Whitcombe</strong><span>Portfolio Manager, Whitcombe Holdings</span></div>
    <div class="arrows">
      <span><svg viewBox="0 0 14 14" fill="none" stroke="#333" stroke-width="1.6"><path d="M12 7H2M6 3L2 7l4 4"/></svg></span>
      <span><svg viewBox="0 0 14 14" fill="none" stroke="#333" stroke-width="1.6"><path d="M2 7h10M8 3l4 4-4 4"/></svg></span>
    </div>
  </article>
</section>

<section class="contact">
  <div class="wrap">
    <div class="contact-copy">
      <div class="eyebrow">Get in touch</div>
      <h2><span class="accent">Request</span> a Tailored <span class="accent">Proposal</span></h2>
      <p>Submit the form to initiate a consultative assessment and explore solutions aligned with your investment objectives.</p>
      <ul class="channels">
        <li><span class="icon"><svg viewBox="0 0 24 24" fill="#fff"><path d="M6.6 10.8a15.1 15.1 0 0 0 6.6 6.6l2.2-2.2c.3-.3.7-.4 1-.2 1.1.4 2.3.6 3.6.6.6 0 1 .4 1 1V20c0 .6-.4 1-1 1A17 17 0 0 1 3 4c0-.6.4-1 1-1h3.5c.6 0 1 .4 1 1 0 1.3.2 2.5.6 3.6.1.3 0 .7-.2 1z"/></svg></span><div><small>Phone</small><b>(216) 555-0148</b></div></li>
        <li><span class="icon"><svg viewBox="0 0 24 24" fill="#fff"><path d="M3 5h18v14H3z"/><path d="M3 6l9 7 9-7" fill="none" stroke="#585a5f" stroke-width="2"/></svg></span><div><small>Email</small><b>info@larkfieldridgemanagement.com</b></div></li>
        <li><span class="icon"><svg viewBox="0 0 24 24" fill="#fff"><path d="M12 2a7 7 0 0 0-7 7c0 5 7 13 7 13s7-8 7-13a7 7 0 0 0-7-7zm0 9.5A2.5 2.5 0 1 1 12 6.5a2.5 2.5 0 0 1 0 5z"/></svg></span><div><small>Office</small><b>Maple Hollow, OH 44990</b></div></li>
      </ul>
    </div>
    <form class="form-card">
      <div class="form-grid">
        <div class="field"><label>Full Name</label><div class="input">Enter your name</div></div>
        <div class="field"><label>Email</label><div class="input">Your@email.com</div></div>
        <div class="field"><label>Phone</label><div class="input">(123) 789-123</div></div>
        <div class="field"><label>Property Type</label><div class="input">Select Type<svg viewBox="0 0 14 14" fill="none" stroke="#333" stroke-width="1.8"><path d="M3 5l4 4 4-4"/></svg></div></div>
        <div class="field full"><label>Message</label><div class="input">Tell us about your property management needs...</div></div>
      </div>
      <div class="submit"><span>Submit Inquiry <svg viewBox="0 0 12 12" fill="none" stroke="#fff" stroke-width="2"><path d="M1 6h9M6 2l4 4-4 4"/></svg></span></div>
    </form>
  </div>
</section>

<footer class="site-footer">
  <div class="wrap">
    <div class="footer-top">
      <div class="footer-brand">
        <div class="brand"><span class="brand-mark"></span>Larkfield Ridge</div>
        <ul>
          <li><svg viewBox="0 0 24 24" fill="#fff"><path d="M6.6 10.8a15.1 15.1 0 0 0 6.6 6.6l2.2-2.2c.3-.3.7-.4 1-.2 1.1.4 2.3.6 3.6.6.6 0 1 .4 1 1V20c0 .6-.4 1-1 1A17 17 0 0 1 3 4c0-.6.4-1 1-1h3.5c.6 0 1 .4 1 1 0 1.3.2 2.5.6 3.6.1.3 0 .7-.2 1z"/></svg>(216) 555-0148</li>
          <li><svg viewBox="0 0 24 24" fill="#fff"><path d="M3 5h18v14H3z"/><path d="M3 6l9 7 9-7" fill="none" stroke="#2a3f6e" stroke-width="2"/></svg>info@larkfieldridgemanagement.com</li>
          <li><svg viewBox="0 0 24 24" fill="#fff"><path d="M12 2a7 7 0 0 0-7 7c0 5 7 13 7 13s7-8 7-13a7 7 0 0 0-7-7zm0 9.5A2.5 2.5 0 1 1 12 6.5a2.5 2.5 0 0 1 0 5z"/></svg>Maple Hollow, OH 44990</li>
        </ul>
      </div>
      <ul class="footer-col col-services"><h4>Services</h4><li>Full-Service Management</li><li>Asset Preservation</li><li>Maintenance Coordination</li><li>Financial Reporting</li><li>Tenant Screening</li></ul>
      <ul class="footer-col col-company"><h4>Company</h4><li>About Us</li><li>Our Team</li><li>Careers</li><li>Blog</li><li>Contact</li></ul>
      <ul class="footer-col"><h4>Legal</h4><li>Privacy Policy</li><li>Terms of Service</li><li>Fair Housing</li><li>Accessibility</li></ul>
    </div>
    <div class="footer-bottom"><span>© 2026 Larkfield Ridge Management LLC. All rights reserved.</span><span>Licensed · Insured · Bonded</span></div>
  </div>
</footer>

</body>
</html>
```